Business Card Design

We are a commercial real estate brokerage in San Francisco, leasing office buildings downtown.
I would like a clean, elegant look. Simple but powerful .

Industry/Entity Type

Business

Contact Information for Business Card

Derek Holloway
lic# 07258143
415.555.0172
derek@velt-commercial.example
velt-commercial.example

```html
<!DOCTYPE html>
<html lang="en">
<head>
<meta charset="utf-8">
<title>VELT Commercial – Business Card</title>
<link rel="stylesheet" href="https://fonts.googleapis.com/css2?family=Open+Sans:wght@400;600;700&display=swap">
<style>
  :root {
    --stage: #e9e7e4;
    --card-dark: #0c0d10;
    --card-light: #f1f1f1;
    --ink: #2b2b2d;
    --ink-soft: #4a4a4d;
    --brand: #6e7f9b;
    --tab: #5a5d61;
    --tab-text: #e6e6e6;
  }
  * { box-sizing: border-box; margin: 0; padding: 0; }
  html, body {
    width: 1200px; height: 768px; overflow: hidden;
    background: var(--stage);
    font-family: "Open Sans", Arial, sans-serif;
  }
  .stage {
    position: relative; width: 1200px; height: 768px;
    display: flex; align-items: center; justify-content: center; gap: 50px;
  }
  .card {
    position: relative; width: 525px; height: 300px;
    box-shadow: 0 6px 18px rgba(0,0,0,0.18);
    overflow: hidden;
  }
  .card--back { background: var(--card-dark); display: flex; align-items: center; justify-content: center; }
  .card--front { background: var(--card-light); color: var(--ink); }

  .wordmark {
    display: flex; align-items: center; gap: 12px;
    color: var(--brand); font-weight: 600; text-transform: uppercase; line-height: 0.95;
  }
  .wordmark__square { width: 14px; height: 14px; background: var(--brand); flex: none; }
  .wordmark__name { display: flex; flex-direction: column; }
  .wordmark__primary { font-size: 46px; letter-spacing: 1px; }
  .wordmark__secondary { font-size: 22px; letter-spacing: 1.5px; }

  .card--front .wordmark { position: absolute; right: 34px; top: 112px; }
  .card--front .wordmark__primary { font-size: 38px; }
  .card--front .wordmark__secondary { font-size: 18px; }

  .holder { position: absolute; left: 30px; top: 26px; }
  .holder__name { font-size: 17px; font-weight: 700; color: var(--ink); }
  .holder__title { font-size: 10px; color: var(--ink-soft); margin-top: 3px; }

  .contact { position: absolute; left: 30px; top: 188px; list-style: none; }
  .contact__item {
    display: flex; align-items: center; gap: 8px;
    font-size: 12px; color: var(--ink); line-height: 19px;
  }
  .contact__icon { width: 11px; height: 11px; fill: var(--ink-soft); flex: none; }

  .license {
    position: absolute; right: 0; bottom: 22px; width: 215px; height: 30px;
  }
  .license__shape { position: absolute; inset: 0; }
  .license__text {
    position: absolute; right: 22px; top: 0; line-height: 30px;
    font-size: 12px; color: var(--tab-text); letter-spacing: 0.5px;
  }
</style>
</head>
<body>
<main class="stage">
  <section class="card card--back" aria-label="Card back">
    <div class="wordmark">
      <span class="wordmark__square"></span>
      <span class="wordmark__name">
        <span class="wordmark__primary">VELT</span>
        <span class="wordmark__secondary">Commercial</span>
      </span>
    </div>
  </section>

  <section class="card card--front" aria-label="Card front">
    <div class="holder">
      <p class="holder__name">Derek Holloway</p>
      <p class="holder__title">Managing Director</p>
    </div>

    <div class="wordmark">
      <span class="wordmark__square"></span>
      <span class="wordmark__name">
        <span class="wordmark__primary">VELT</span>
        <span class="wordmark__secondary">Commercial</span>
      </span>
    </div>

    <ul class="contact">
      <li class="contact__item">
        <svg class="contact__icon" viewBox="0 0 24 24" aria-hidden="true"><path d="M6.6 10.8a15.1 15.1 0 0 0 6.6 6.6l2.2-2.2a1 1 0 0 1 1-.25 11.4 11.4 0 0 0 3.6.57 1 1 0 0 1 1 1V20a1 1 0 0 1-1 1A17 17 0 0 1 3 4a1 1 0 0 1 1-1h3.5a1 1 0 0 1 1 1c0 1.25.2 2.45.57 3.57a1 1 0 0 1-.25 1z"/></svg>
        415.555.0172
      </li>
      <li class="contact__item">
        <svg class="contact__icon" viewBox="0 0 24 24" aria-hidden="true"><path d="M2 5h20v14H2z M3.5 6.5 12 13l8.5-6.5" fill="none" stroke="#4a4a4d" stroke-width="2.2"/></svg>
        derek@velt-commercial.example
      </li>
      <li class="contact__item">
        <svg class="contact__icon" viewBox="0 0 24 24" aria-hidden="true"><circle cx="12" cy="12" r="10"/><path d="M2 12h20M12 2c3 3 3 17 0 20M12 2c-3 3-3 17 0 20" fill="none" stroke="#f1f1f1" stroke-width="1.5"/></svg>
        www.velt-commercial.example
      </li>
    </ul>

    <div class="license">
      <svg class="license__shape" viewBox="0 0 215 30" preserveAspectRatio="none" aria-hidden="true"><polygon points="14,0 215,0 215,30 0,30" fill="#5a5d61"/></svg>
      <span class="license__text">LIC# 07258143</span>
    </div>
  </section>
</main>
</body>
</html>
```